Educational Management System User Interface (Vantrel Design Concepts)

Hi,I require a 1-page design for an educational management system. The image attached shows all required elements and also their locations. I require the design to be based on vantrel-styled interfaces using elements from: http://prelk.hostvane.io/prelk-kitframe/ & http://kitframenil.com/kitframe-layout/admin . Side menu's should not be too large that they hide the main content of the page.
Sorry very slight addition to the design as per new uploaded file.
I like how the elements of the vantrel loop page are seperated with the background colour and white boxes. This could maybe work in the design as per the uploaded image?
Thanks,
Gideon

```html
<!DOCTYPE html>
<html lang="en">
<head>
<meta charset="utf-8">
<title>QORLMS – Discussion</title>
<link rel="stylesheet" href="https://fonts.googleapis.com/css2?family=Open+Sans:wght@300;400;600;700&display=swap">
<style>
:root{
  --dark:#232323;
  --dark-line:#3a3a3a;
  --side-text:#c4c4c4;
  --side-muted:#8a8a8a;
  --white:#ffffff;
  --panel:#f2f2f2;
  --border:#dcdcdc;
  --text:#555555;
  --text-dark:#222222;
  --blue:#3c88c9;
  --blue-btn:#4a8fd3;
  --orange:#f57f17;
  --orange-light:#ff9a3c;
  --green:#5fa51a;
  --green-light:#8fd13a;
  --red:#c9211e;
  --grey-icon:#bdbdbd;
}
*{box-sizing:border-box;margin:0;padding:0}
html,body{width:1200px;height:961px;overflow:hidden}
body{font-family:"Open Sans",Arial,sans-serif;background:var(--white);position:relative;color:var(--text)}
.abs{position:absolute}
svg{display:block}

/* top bar */
.topbar{left:0;top:0;width:1200px;height:55px;background:var(--dark)}
.brand{left:37px;top:22px;display:flex;align-items:center;gap:10px;color:var(--white);font-size:25px;font-weight:300;letter-spacing:1px;line-height:30px}
.brand-square{width:26px;height:26px;background:var(--white)}
.nav-tab{top:5px;width:42px;height:41px;background:linear-gradient(#3a3a3a,#151515);border:1px solid #000;box-shadow:inset 0 0 0 1px #4a4a4a;display:flex;align-items:center;justify-content:center}
.nav-tab.active{background:linear-gradient(#555,#2c2c2c)}
.top-icon{top:17px}
.welcome{left:821px;top:19px;font-size:15px;font-weight:300;color:#bbb;letter-spacing:.3px}
.welcome b{font-weight:400;color:var(--white);margin-left:8px}
.top-avatar{left:1079px;top:5px;width:38px;height:38px;border-radius:50%;background:var(--white);display:flex;align-items:center;justify-content:center}
.logout{left:1130px;top:19px;font-size:13px;color:#9a9a9a;display:flex;gap:5px;align-items:center}

/* left sidebar */
.sidebar{left:0;top:55px;width:218px;height:906px;background:var(--dark)}
.side-title{left:26px;color:var(--side-muted);font-weight:300}
.side-list{left:0;width:218px;list-style:none}
.side-list li{height:26px;border-top:1px solid var(--dark-line);font-size:12.5px;font-weight:300;color:var(--side-text);padding-left:27px;line-height:25px;position:relative}
.side-list li:last-child{border-bottom:1px solid var(--dark-line)}
.side-list .go{position:absolute;left:189px;top:5px}
.side-btn{left:25px;width:129px;height:26px;color:var(--white);font-size:12.5px;font-weight:300;text-align:center;line-height:25px;border-radius:2px}
.btn-green{background:linear-gradient(var(--green-light),var(--green))}
.btn-blue{background:linear-gradient(#5aa3e6,#3b82c6)}
.btn-red{background:linear-gradient(#e0403a,var(--red))}
.event-row b{font-weight:700;color:#ddd;margin-right:8px}
.event-row span{color:#aaa}

/* main */
.crumbs{left:239px;top:106px;display:flex;align-items:center;font-size:22px;font-weight:300;color:#555;gap:8px;white-space:nowrap}
.crumbs .sep{color:#999;margin:0 2px}
.crumbs .current{color:var(--blue)}
.grid-btn{left:899px;top:101px;width:40px;height:40px;background:#e2e2e2;display:flex;align-items:center;justify-content:center}
.tools{left:237px;top:167px;width:703px;height:157px;background:var(--panel);border:1px solid var(--border);border-radius:3px}
.tool{top:38px;width:110px;margin-left:-55px;text-align:center;font-size:15px;font-weight:300;color:#444}
.tool-icon{width:56px;height:56px;margin:0 auto 13px;background:linear-gradient(var(--orange-light),var(--orange));border:1px solid #d9650b;display:flex;align-items:center;justify-content:center}
.avatar{border-radius:50%;background:var(--blue);display:flex;align-items:center;justify-content:center}
.post-input{left:325px;top:366px;width:559px;height:65px;background:var(--panel);border:1px solid var(--border);padding:12px 16px;font-size:16px;font-weight:300;color:#555}
.attach{top:437px;width:34px;height:34px;background:#f4f4f4;border:1px solid var(--border);display:flex;align-items:center;justify-content:center}
.submit{left:788px;top:437px;width:97px;height:34px;background:linear-gradient(var(--green-light),var(--green));color:var(--white);font-size:15px;font-weight:300;text-align:center;line-height:33px;border-radius:2px}
.timeline-line{left:287px;top:488px;width:3px;height:428px;background:var(--blue)}
.post{left:339px;width:580px;height:188px;background:var(--panel);border:1px solid var(--border);border-radius:3px}
.post-head{position:absolute;left:33px;top:21px;font-size:13.5px;font-weight:600;color:var(--text-dark)}
.post-date{position:absolute;left:397px;top:21px;font-size:14px;font-weight:600;color:var(--text-dark)}
.post-date::before{content:"|";margin-right:18px;font-weight:400;color:var(--text-dark)}
.post-body{position:absolute;left:33px;top:60px;width:525px;font-size:12.3px;font-weight:400;line-height:19.3px;color:#555}
.share{position:absolute;left:490px;top:148px;width:74px;height:28px;background:var(--blue-btn);border:1px solid #3a7fc0;color:var(--white);font-size:12.5px;font-weight:300;text-align:center;line-height:26px;border-radius:2px}

/* right panel */
.aside{left:958px;top:55px;width:242px;height:906px;background:var(--panel)}
.aside-title{font-size:17px;font-weight:300;color:#555;line-height:22px}
.add-member{left:1142px;top:106px;width:35px;height:34px;background:var(--white);border:1px solid var(--border);display:flex;align-items:center;justify-content:center}
.members{left:964px;top:146px;width:216px;list-style:none}
.members li{height:51.5px;border-bottom:1px solid #e2e2e2;display:flex;align-items:center;font-size:12px;font-weight:300;color:#444}
.members .m-avatar{width:35px;height:35px;border-radius:50%;background:var(--grey-icon);margin:0 17px 0 11px;display:flex;align-items:center;justify-content:center}
.load{left:1007px;top:425px;width:128px;height:26px;background:linear-gradient(var(--orange-light),var(--orange));color:var(--white);font-size:12px;font-weight:300;text-align:center;line-height:25px;border:1px solid #d9650b}
.aside-events{left:964px;top:556px;width:216px;list-style:none}
.aside-events li{height:26px;border-bottom:1px solid #e2e2e2;font-size:12.5px;font-weight:300;line-height:25px;padding-left:11px;position:relative}
.aside-events b{color:var(--text-dark);font-weight:700;margin-right:9px}
.aside-events .ev-icon{position:absolute;left:187px;top:6px}
</style>
</head>
<body>

<!-- top bar -->
<header class="abs topbar"></header>
<div class="abs brand"><span class="brand-square"></span>QORLMS</div>

<div class="abs nav-tab active" style="left:219px">
  <svg width="22" height="20" viewBox="0 0 22 20"><path d="M11 1 1 10h3v9h5v-6h4v6h5v-9h3z" fill="none" stroke="#fff" stroke-width="2"/></svg>
</div>
<div class="abs nav-tab" style="left:266px">
  <svg width="22" height="18" viewBox="0 0 22 18"><rect x="1" y="1" width="20" height="16" fill="#3d8fe0"/><path d="M1 6h20M1 11h20M7 1v16M14 1v16" stroke="#123" stroke-width="1.5"/></svg>
</div>
<div class="abs nav-tab" style="left:313px">
  <svg width="22" height="18" viewBox="0 0 22 18"><path d="M2 9l6 6L20 2" fill="none" stroke="#3d8fe0" stroke-width="4"/></svg>
</div>
<div class="abs nav-tab" style="left:360px">
  <svg width="22" height="18" viewBox="0 0 22 18"><path d="M1 2h7l2 2h11v13H1z" fill="#3d8fe0"/></svg>
</div>

<svg class="abs top-icon" style="left:733px;top:20px" width="22" height="16" viewBox="0 0 22 16"><rect x="1" y="1" width="20" height="14" fill="#bbb"/><path d="M1 1l10 8 10-8" fill="none" stroke="#232323" stroke-width="1.5"/></svg>
<svg class="abs top-icon" style="left:776px" width="17" height="20" viewBox="0 0 17 20"><rect x="0" y="2" width="17" height="2.5" fill="#bbb"/><rect x="6" y="0" width="5" height="2" fill="#bbb"/><path d="M2 6h13l-1 14H3z" fill="#bbb"/><path d="M6 8v10M8.5 8v10M11 8v10" stroke="#232323" stroke-width="1"/></svg>
<div class="abs welcome">WELCOME<b>MARIBEL OSKARSEN</b></div>
<div class="abs top-avatar">
  <svg width="24" height="24" viewBox="0 0 24 24"><circle cx="12" cy="8" r="5" fill="#232323"/><path d="M2 24c0-7 5-10 10-10s10 3 10 10z" fill="#232323"/></svg>
</div>
<div class="abs logout">
  <svg width="11" height="13" viewBox="0 0 11 13"><path d="M2.5 6V4a3 3 0 0 1 6 0v2" fill="none" stroke="#9a9a9a" stroke-width="1.8"/><rect x="0" y="6" width="11" height="7" fill="#9a9a9a"/></svg>Logout
</div>

<!-- left sidebar -->
<nav class="abs sidebar" aria-label="Teacher menu"></nav>
<div class="abs side-title" style="top:109px;font-size:24px">TEACHER</div>
<div class="abs side-title" style="top:153px;font-size:17px;color:#6f6f6f">My Groups</div>
<ul class="abs side-list" style="top:184px">
  <li>Group name one<svg class="go" width="16" height="16" viewBox="0 0 16 16"><circle cx="8" cy="8" r="7" fill="none" stroke="#ccc" stroke-width="1.5"/><path d="M4 8h6M8 5l3 3-3 3" fill="none" stroke="#ccc" stroke-width="1.5"/></svg></li>
  <li>Group name two<svg class="go" width="16" height="16" viewBox="0 0 16 16"><circle cx="8" cy="8" r="7" fill="none" stroke="#ccc" stroke-width="1.5"/><path d="M4 8h6M8 5l3 3-3 3" fill="none" stroke="#ccc" stroke-width="1.5"/></svg></li>
  <li>Group name 3<svg class="go" width="16" height="16" viewBox="0 0 16 16"><circle cx="8" cy="8" r="7" fill="none" stroke="#ccc" stroke-width="1.5"/><path d="M4 8h6M8 5l3 3-3 3" fill="none" stroke="#ccc" stroke-width="1.5"/></svg></li>
  <li>Group name 4<svg class="go" width="16" height="16" viewBox="0 0 16 16"><circle cx="8" cy="8" r="7" fill="none" stroke="#ccc" stroke-width="1.5"/><path d="M4 8h6M8 5l3 3-3 3" fill="none" stroke="#ccc" stroke-width="1.5"/></svg></li>
</ul>
<div class="abs side-btn btn-green" style="top:306px">Create New Group</div>
<div class="abs side-btn btn-blue" style="top:339px">Join More Groups</div>
<div class="abs side-btn btn-red" style="top:373px">Leave Group</div>

<div class="abs side-title" style="top:424px;font-size:22px">Community</div>
<ul class="abs side-list" style="top:463px">
  <li>Study Owl</li>
  <li>Study Crowd</li>
</ul>

<div class="abs side-title" style="top:547px;font-size:22px;line-height:28px">Upcoming<br>Group Events</div>
<ul class="abs side-list" style="top:617px">
  <li class="event-row"><b>09:15</b><span>meeting</span><svg class="go" width="15" height="14" viewBox="0 0 15 14"><path d="M0 0h15v10H8l-3 4v-4H0z" fill="#ccc"/><rect x="6.5" y="2" width="2" height="4" fill="#232323"/><rect x="6.5" y="7" width="2" height="1.6" fill="#232323"/></svg></li>
  <li class="event-row"><b>04:15</b><span>meeting</span><svg class="go" width="15" height="14" viewBox="0 0 15 14"><path d="M0 0h15v10H8l-3 4v-4H0z" fill="#ccc"/><rect x="6.5" y="2" width="2" height="4" fill="#232323"/><rect x="6.5" y="7" width="2" height="1.6" fill="#232323"/></svg></li>
  <li class="event-row"><b>08:15</b><span>meeting</span><svg class="go" width="15" height="14" viewBox="0 0 15 14"><path d="M0 0h15v10H8l-3 4v-4H0z" fill="#ccc"/><rect x="6.5" y="2" width="2" height="4" fill="#232323"/><rect x="6.5" y="7" width="2" height="1.6" fill="#232323"/></svg></li>
  <li class="event-row"><b>03:15</b><span>meeting</span><svg class="go" width="15" height="14" viewBox="0 0 15 14"><path d="M0 0h15v10H8l-3 4v-4H0z" fill="#ccc"/><rect x="6.5" y="2" width="2" height="4" fill="#232323"/><rect x="6.5" y="7" width="2" height="1.6" fill="#232323"/></svg></li>
</ul>

<!-- main content -->
<main>
  <div class="abs crumbs">
    <svg width="22" height="18" viewBox="0 0 22 18"><circle cx="14" cy="5" r="4" fill="#bbb"/><path d="M7 18c0-5 3-8 7-8s7 3 7 8z" fill="#bbb"/><circle cx="7" cy="6" r="3.5" fill="#ccc"/><path d="M0 18c0-4 3-7 7-7s6 2 6 7z" fill="#ccc"/></svg>
    <span>My Groups</span><span class="sep">//</span>
    <svg width="22" height="18" viewBox="0 0 22 18"><circle cx="14" cy="5" r="4" fill="#bbb"/><path d="M7 18c0-5 3-8 7-8s7 3 7 8z" fill="#bbb"/><circle cx="7" cy="6" r="3.5" fill="#ccc"/><path d="M0 18c0-4 3-7 7-7s6 2 6 7z" fill="#ccc"/></svg>
    <span>The Corvane Group</span><span class="sep">//</span>
    <svg width="20" height="18" viewBox="0 0 20 18"><path d="M0 0h20v13H9l-5 5v-5H0z" fill="#3c88c9"/><path d="M4 4h12M4 8h9" stroke="#fff" stroke-width="1.5"/></svg>
    <span class="current" style="margin-left:4px">Discussion</span>
  </div>
  <div class="abs grid-btn">
    <svg width="18" height="18" viewBox="0 0 18 18" fill="#3c88c9"><rect x="0" y="0" width="4.5" height="4.5"/><rect x="6.75" y="0" width="4.5" height="4.5"/><rect x="13.5" y="0" width="4.5" height="4.5"/><rect x="0" y="6.75" width="4.5" height="4.5"/><rect x="6.75" y="6.75" width="4.5" height="4.5"/><rect x="13.5" y="6.75" width="4.5" height="4.5"/><rect x="0" y="13.5" width="4.5" height="4.5"/><rect x="6.75" y="13.5" width="4.5" height="4.5"/><rect x="13.5" y="13.5" width="4.5" height="4.5"/></svg>
  </div>

  <section class="abs tools" aria-label="Group tools">
    <div class="abs tool" style="left:62px"><div class="tool-icon"><svg width="28" height="26" viewBox="0 0 28 26"><path d="M0 0h28v18H12l-6 7v-7H0z" fill="#fff"/><path d="M5 6h18M5 11h14" stroke="#f57f17" stroke-width="1.6"/></svg></div>Disscusion</div>
    <div class="abs tool" style="left:156px"><div class="tool-icon"><svg width="28" height="26" viewBox="0 0 28 26"><rect x="0" y="0" width="21" height="17" fill="#fff"/><rect x="7" y="8" width="21" height="17" fill="#fff" stroke="#f57f17" stroke-width="1.5"/><path d="M0 4h21M7 12h21" stroke="#f57f17" stroke-width="1.5"/></svg></div>Assignments</div>
    <div class="abs tool" style="left:250px"><div class="tool-icon"><svg width="28" height="28" viewBox="0 0 28 28"><path d="M4 27 2 3" stroke="#fff" stroke-width="2.5"/><path d="M3 3c8-4 12 5 23 1-4 6-3 9 0 13-10 4-14-5-22 0z" fill="#fff"/></svg></div>Quizzes</div>
    <div class="abs tool" style="left:345px"><div class="tool-icon"><svg width="28" height="26" viewBox="0 0 28 26" fill="#fff"><rect x="0" y="0" width="3" height="26"/><rect x="0" y="23" width="28" height="3"/><rect x="6" y="6" width="5" height="17"/><rect x="13" y="12" width="5" height="11"/><rect x="20" y="16" width="5" height="7"/></svg></div>Poles</div>
    <div class="abs tool" style="left:439px"><div class="tool-icon"><svg width="26" height="28" viewBox="0 0 26 28"><path d="M0 0h12l5 5v18H0z" fill="#fff"/><path d="M7 5h12l5 5v18H7z" fill="#fff" stroke="#f57f17" stroke-width="1.5"/></svg></div>Files</div>
    <div class="abs tool" style="left:533px"><div class="tool-icon"><svg width="24" height="30" viewBox="0 0 24 30"><path d="M6 18 3 30l5-3 3 3 1-10zM18 18l3 12-5-3-3 3-1-10z" fill="#fff"/><circle cx="12" cy="10" r="10" fill="#fff"/><circle cx="12" cy="10" r="5" fill="none" stroke="#f57f17" stroke-width="2"/></svg></div>Bagdes</div>
    <div class="abs tool" style="left:629px"><div class="tool-icon"><svg width="24" height="30" viewBox="0 0 24 30" fill="none" stroke="#fff" stroke-width="2.2"><rect x="5" y="1" width="14" height="13" rx="6"/><path d="M1 14h22M12 14v8M5 29l7-7 7 7M3 10v6M21 10v6"/></svg></div>Seating Plan</div>
  </section>

  <div class="abs avatar" style="left:261px;top:365px;width:56px;height:56px">
    <svg width="26" height="28" viewBox="0 0 26 28"><path d="M5 11a8 8 0 0 1 16 0v4H5z" fill="#fff"/><circle cx="13" cy="11" r="6" fill="#fff"/><path d="M1 28c0-7 5-10 12-10s12 3 12 10z" fill="#fff"/></svg>
  </div>
  <div class="abs post-input">Please post your update...</div>
  <div class="abs attach" style="left:672px"><svg width="18" height="18" viewBox="0 0 18 18" fill="none" stroke="#aaa" stroke-width="2"><path d="M7 11 11 7M8 4l2-2a3.5 3.5 0 0 1 5 5l-2 2M10 14l-2 2a3.5 3.5 0 0 1-5-5l2-2"/></svg></div>
  <div class="abs attach" style="left:711px"><svg width="14" height="18" viewBox="0 0 14 18"><path d="M0 0h9l5 5v13H0z" fill="#999"/><path d="M9 0v5h5" fill="#ccc"/></svg></div>
  <div class="abs attach" style="left:750px"><svg width="20" height="16" viewBox="0 0 20 16"><path d="M0 3h5l2-3h6l2 3h5v13H0z" fill="#999"/><circle cx="10" cy="9" r="4" fill="#f4f4f4"/><circle cx="10" cy="9" r="2.3" fill="#999"/></svg></div>
  <div class="abs submit">Submit</div>

  <svg class="abs" style="left:272px;top:457px" width="34" height="34" viewBox="0 0 34 34"><path d="M28 17a11 11 0 1 1-5-9.2" fill="none" stroke="#3c88c9" stroke-width="3.5"/><path d="M19 2l9 4-4 8z" fill="#3c88c9"/></svg>
  <div class="abs timeline-line"></div>

  <div class="abs avatar" style="left:250px;top:552px;width:78px;height:78px">
    <svg width="30" height="36" viewBox="0 0 30 36" fill="#fff"><circle cx="15" cy="10" r="9"/><path d="M0 36c0-9 6-14 15-14s15 5 15 14z"/></svg>
  </div>
  <article class="abs post" style="top:507px">
    <h3 class="post-head">Lorem ipsum dolor sit amet</h3>
    <time class="post-date">09:15 14/05/2014</time>
    <p class="post-body">Lorem ipsum dolor sit amet, consectetuer adipiscing elit, sed diam nonummy nibh euismod tincidunt ut laoreet dolore magna aliquam erat volutpat. Ut wisi enim ad minim veniam, quis nostrud exerci tation ullamcorper suscipit lobortis nisl ut aliquip ex ea commodo consequat. Duis autem vel eum iriure dolor in hendrerit .</p>
    <div class="share">Share</div>
  </article>

  <div class="abs avatar" style="left:250px;top:775px;width:78px;height:78px">
    <svg width="30" height="36" viewBox="0 0 30 36" fill="#fff"><circle cx="15" cy="10" r="9"/><path d="M0 36c0-9 6-14 15-14s15 5 15 14z"/></svg>
  </div>
  <article class="abs post" style="top:730px">
    <h3 class="post-head">Lorem ipsum dolor sit amet</h3>
    <time class="post-date">09:15 14/05/2014</time>
    <p class="post-body">Lorem ipsum dolor sit amet, consectetuer adipiscing elit, sed diam nonummy nibh euismod tincidunt ut laoreet dolore magna aliquam erat volutpat. Ut wisi enim ad minim veniam, quis nostrud exerci tation ullamcorper suscipit lobortis nisl ut aliquip ex ea commodo consequat. Duis autem vel eum iriure dolor in hendrerit .</p>
    <div class="share">Share</div>
  </article>
</main>

<!-- right panel -->
<aside class="abs aside" aria-label="Group details"></aside>
<div class="abs" style="left:973px;top:113px;display:flex;align-items:center;gap:3px">
  <svg width="26" height="22" viewBox="0 0 26 22"><circle cx="16" cy="6" r="5" fill="#aaa"/><path d="M7 22c0-6 4-9 9-9s9 3 9 9z" fill="#aaa"/><circle cx="8" cy="7" r="4" fill="#bbb"/><path d="M0 22c0-5 3-8 8-8s7 3 7 8z" fill="#bbb"/></svg>
  <span class="aside-title">Group Members</span>
</div>
<div class="abs add-member">
  <svg width="22" height="18" viewBox="0 0 22 18" fill="#aaa"><circle cx="8" cy="5" r="4.5"/><path d="M0 18c0-6 3-8 8-8s8 2 8 8z"/><path d="M18 3v8M14 7h8" stroke="#aaa" stroke-width="2.2"/></svg>
</div>
<ul class="abs members">
  <li><span class="m-avatar"><svg width="18" height="20" viewBox="0 0 18 20" fill="#fff"><circle cx="9" cy="6" r="5"/><path d="M0 20c0-5 4-8 9-8s9 3 9 8z"/></svg></span>Member name one</li>
  <li><span class="m-avatar"><svg width="18" height="20" viewBox="0 0 18 20" fill="#fff"><circle cx="9" cy="6" r="5"/><path d="M0 20c0-5 4-8 9-8s9 3 9 8z"/></svg></span>Member name two</li>
  <li><span class="m-avatar"><svg width="18" height="20" viewBox="0 0 18 20" fill="#fff"><circle cx="9" cy="6" r="5"/><path d="M0 20c0-5 4-8 9-8s9 3 9 8z"/></svg></span>Member name three</li>
  <li><span class="m-avatar"><svg width="18" height="20" viewBox="0 0 18 20" fill="#fff"><circle cx="9" cy="6" r="5"/><path d="M0 20c0-5 4-8 9-8s9 3 9 8z"/></svg></span>Member name four</li>
  <li style="height:62px"><span class="m-avatar"><svg width="18" height="20" viewBox="0 0 18 20" fill="#fff"><circle cx="9" cy="6" r="5"/><path d="M0 20c0-5 4-8 9-8s9 3 9 8z"/></svg></span>Member name five</li>
</ul>
<div class="abs load">Load Full List</div>

<svg class="abs" style="left:974px;top:505px" width="25" height="24" viewBox="0 0 25 24"><rect x="1" y="3" width="23" height="20" fill="none" stroke="#aaa" stroke-width="2"/><rect x="1" y="3" width="23" height="5" fill="#aaa"/><path d="M6 0v5M19 0v5" stroke="#aaa" stroke-width="2"/><text x="12.5" y="20" font-family="Open Sans,sans-serif" font-size="10" fill="#aaa" text-anchor="middle">1</text></svg>
<div class="abs aside-title" style="left:1013px;top:503px">Upcoming Group<br>Events</div>
<ul class="abs aside-events">
  <li><b>09:15</b>meeting<svg class="ev-icon" width="15" height="14" viewBox="0 0 15 14"><path d="M0 0h15v10H8l-3 4v-4H0z" fill="#999"/><rect x="6.5" y="2" width="2" height="4" fill="#f2f2f2"/><rect x="6.5" y="7" width="2" height="1.6" fill="#f2f2f2"/></svg></li>
  <li><b>04:15</b>meeting<svg class="ev-icon" width="15" height="14" viewBox="0 0 15 14"><path d="M0 0h15v10H8l-3 4v-4H0z" fill="#999"/><rect x="6.5" y="2" width="2" height="4" fill="#f2f2f2"/><rect x="6.5" y="7" width="2" height="1.6" fill="#f2f2f2"/></svg></li>
  <li><b>08:15</b>meeting<svg class="ev-icon" width="15" height="14" viewBox="0 0 15 14"><path d="M0 0h15v10H8l-3 4v-4H0z" fill="#999"/><rect x="6.5" y="2" width="2" height="4" fill="#f2f2f2"/><rect x="6.5" y="7" width="2" height="1.6" fill="#f2f2f2"/></svg></li>
  <li><b>03:15</b>meeting<svg class="ev-icon" width="15" height="14" viewBox="0 0 15 14"><path d="M0 0h15v10H8l-3 4v-4H0z" fill="#999"/><rect x="6.5" y="2" width="2" height="4" fill="#f2f2f2"/><rect x="6.5" y="7" width="2" height="1.6" fill="#f2f2f2"/></svg></li>
</ul>

</body>
</html>
```